Health Supplement Series for 60 tablets of pure Amber Vine Core powder

We need a packaging design theme for a health supplement for international consumers. Our initial product is called 'Amber Vine Core'. It is for general health and is particularly effective for diabetic symptoms.
We would like to see designs that are clean and fresh.
It should give the impression of professional, premium pharmaceutical grade products.
Our company logo is attached below.

Target Market(s)

International

Industry/Entity Type

Health And Wellness

Font styles to use
Serif
Sans Serif

Requirements
Must have
• Bottle and box packaging required.
• 1st product is bottle of 60 tablets of 0.5gm each.
Should not have
• Seals and other "must buy" "guaranteed" etc

```html
<!DOCTYPE html>
<html lang="en">
<head>
<meta charset="UTF-8">
<title>Amber Vine Core – Bottle Label</title>
<link rel="stylesheet" href="https://fonts.googleapis.com/css2?family=Open+Sans:wght@400;700&display=swap">
<style>
  :root {
    --canvas-bg: #eeeeee;
    --label-bg: #ffffff;
    --brown-deep: #5e2412;
    --brown-title: #7b3a20;
    --brown-band: #6a2a14;
    --leaf-green: #4f8a2a;
    --leaf-light: #7cb342;
    --brand-green: #5a9e2f;
    --body-grey: #666666;
    --seed-dark: #6b3a1d;
    --seed-light: #c07a45;
  }
  html, body {
    margin: 0;
    padding: 0;
    width: 1158px;
    height: 1200px;
    overflow: hidden;
    background: var(--canvas-bg);
    font-family: "Open Sans", Arial, sans-serif;
  }
  .label {
    position: absolute;
    left: 259px;
    top: 200px;
    width: 640px;
    height: 795px;
    background: var(--label-bg);
    overflow: hidden;
    box-shadow: 0 2px 10px rgba(0,0,0,0.08);
  }
  .label-bands {
    position: absolute;
    inset: 0;
  }
  .vine {
    position: absolute;
    border-radius: 24px;
  }
  .vine--top {
    left: 20px; top: 48px; width: 380px; height: 34px;
    background: linear-gradient(90deg, rgba(79,138,42,0.45), rgba(124,179,66,0.3), rgba(79,138,42,0.45));
  }
  .vine--left {
    left: 4px; top: 96px; width: 42px; height: 350px;
    background: linear-gradient(180deg, rgba(79,138,42,0.45), rgba(124,179,66,0.25), rgba(79,138,42,0.4));
  }
  .vine--right {
    left: 548px; top: 64px; width: 46px; height: 236px;
    background: linear-gradient(180deg, rgba(124,179,66,0.45), rgba(79,138,42,0.4), rgba(124,179,66,0.2));
  }
  .wrap-edge {
    position: absolute;
    right: 0;
    width: 16px;
    background: var(--leaf-light);
  }
  .wrap-edge--top { top: 0; height: 18px; }
  .wrap-edge--bottom { top: 650px; height: 80px; background: var(--leaf-green); }
  .brand {
    position: absolute;
    left: 0;
    right: 0;
    top: 126px;
    display: flex;
    justify-content: center;
    align-items: center;
    gap: 6px;
    color: var(--brand-green);
    font-weight: 700;
  }
  .brand-mark {
    width: 26px;
    height: 34px;
    background: var(--brand-green);
  }
  .brand-name { line-height: 1; }
  .brand-line-main {
    display: block;
    font-size: 28px;
    letter-spacing: 2px;
  }
  .brand-line-sub {
    display: block;
    font-size: 10px;
    letter-spacing: 0.5px;
    margin-top: 2px;
  }
  .product-title {
    position: absolute;
    left: 60px;
    width: 480px;
    top: 206px;
    margin: 0;
    text-align: center;
    color: var(--brown-title);
    font-weight: 700;
    font-size: 64px;
    line-height: 1.28;
    letter-spacing: 0.5px;
  }
  .product-visual {
    position: absolute;
    left: 200px;
    top: 440px;
    width: 210px;
    height: 200px;
    border-radius: 50%;
    background: radial-gradient(ellipse at 50% 45%, var(--seed-light) 0%, var(--seed-dark) 55%, rgba(107,58,29,0.5) 66%, rgba(107,58,29,0) 70%);
  }
  .product-copy {
    position: absolute;
    left: 125px;
    width: 360px;
    top: 668px;
    margin: 0;
    font-size: 14px;
    line-height: 1.4;
    color: var(--body-grey);
    text-align: center;
  }
</style>
</head>
<body>
  <section class="label">
    <svg class="label-bands" viewBox="0 0 640 795" width="640" height="795" aria-hidden="true">
      <path d="M0,6 C120,-2 260,4 380,22 C480,36 580,46 640,44 L640,54 C570,58 470,48 370,34 C250,16 120,10 0,16 Z" fill="var(--brown-band)"/>
      <path d="M0,740 C90,724 180,748 300,795 L0,795 Z" fill="var(--brown-band)"/>
      <path d="M0,760 C100,748 220,770 320,795 L300,795 C200,774 100,756 0,770 Z" fill="var(--brown-deep)" opacity="0.6"/>
      <path d="M300,795 C420,775 540,768 640,766 L640,772 C540,774 420,782 320,795 Z" fill="var(--brown-band)"/>
    </svg>

    <div class="vine vine--top" role="img" aria-label="Climbing ivy vine along the top band"></div>
    <div class="vine vine--left" role="img" aria-label="Ivy vine hanging down the left edge"></div>
    <div class="vine vine--right" role="img" aria-label="Ivy vine hanging down the right edge"></div>
    <div class="wrap-edge wrap-edge--top"></div>
    <div class="wrap-edge wrap-edge--bottom"></div>

    <div class="brand">
      <span class="brand-mark"></span>
      <span class="brand-name">
        <span class="brand-line-main">CORVALE</span>
        <span class="brand-line-sub">BIOTECH LIMITED</span>
      </span>
    </div>

    <h1 class="product-title">AMBER VINE<br>CORE</h1>

    <div class="product-visual" role="img" aria-label="Photo of cracked brown seeds"></div>

    <p class="product-copy">Lorem ipsum dolor sit amet, consectetur adipiscing elit. Ut mollis lobortis tempus. Donec lobortis</p>
  </section>
</body>
</html>
```